real esate business card with company logo and name

we need a business card design for a real esate company

The company name is Walsh & Brand Pty Ltd, and we have our logo designed and will upload. We want classic or moden feel. Black or white background. looks more textured. Should include folowinginformations
Owen Walsh and Lucy Brand
Sales Agents & Onsite Manager
p: 07 5948 2063
F: 07 5948 2174
M:0431 857 219
3/42 Marlow Crescent, FERNLEA QLD 4213

We want this business card looks professonal. Thank you in advance.

Industry/Entity Type

Real Estate Agent

Contact Information for Business Card

Owen Walsh and Lucy Brand
Onsite Manager & Sales Agents
p: 07 5948 2063
M:0431 857 219

Font styles to use
Serif

Colors
000000
fbfbfb
333333
959595

Requirements
Must have
• company logo and name, black or white back ground

```html
<!DOCTYPE html>
<html lang="en">
<head>
<meta charset="utf-8">
<title>Walsh &amp; Brand Pty Ltd — Business Card</title>
<link href="https://fonts.googleapis.com/css2?family=Tangerine:wght@700&family=Tinos:wght@400&display=swap" rel="stylesheet">
<style>
  :root {
    --ink: #000000;
    --paper: #fbfbfb;
    --charcoal: #333333;
    --mid-grey: #959595;
    --stage: #e6e6e6;
  }
  html, body {
    margin: 0;
    width: 1200px;
    height: 902px;
    overflow: hidden;
    background: var(--stage);
  }
  .card {
    position: absolute;
    left: 100px;
    top: 165px;
    width: 1000px;
    height: 572px;
    background: var(--paper);
    box-shadow: 0 6px 24px rgba(0,0,0,0.18);
    overflow: hidden;
  }
  .card-art {
    position: absolute;
    inset: 0;
  }
  .brand {
    position: absolute;
    left: 60px;
    top: 250px;
    display: flex;
    align-items: center;
    gap: 10px;
    font-family: "Tinos", serif;
    font-size: 17px;
    letter-spacing: 1px;
    color: var(--mid-grey);
    white-space: nowrap;
  }
  .brand-mark {
    width: 16px;
    height: 16px;
    background: var(--mid-grey);
  }
  .names {
    position: absolute;
    left: 300px;
    top: 62px;
    margin: 0;
    font-family: "Tangerine", cursive;
    font-weight: 700;
    font-size: 66px;
    line-height: 1;
    color: var(--ink);
    white-space: nowrap;
  }
  .role {
    position: absolute;
    left: 440px;
    top: 138px;
    margin: 0;
    font-family: "Tinos", serif;
    font-size: 23px;
    color: var(--ink);
    white-space: nowrap;
  }
  .contact-list {
    position: absolute;
    left: 330px;
    top: 430px;
    margin: 0;
    padding: 0;
    list-style: none;
    font-family: "Tinos", serif;
    font-size: 25px;
    color: var(--paper);
  }
  .contact-list li {
    display: flex;
    align-items: center;
    gap: 14px;
    height: 38px;
    white-space: nowrap;
  }
  .contact-icon {
    width: 22px;
    height: 22px;
    flex: none;
  }
</style>
</head>
<body>
  <article class="card">
    <svg class="card-art" viewBox="0 0 1000 572" width="1000" height="572">
      <defs>
        <linearGradient id="house-tone" x1="0" y1="0" x2="0" y2="1">
          <stop offset="0" stop-color="#8d8f92"/>
          <stop offset="0.55" stop-color="#c9cacb"/>
          <stop offset="1" stop-color="#5d6b55"/>
        </linearGradient>
      </defs>
      <path class="dark-band" d="M140,572 C190,380 400,290 720,318 C480,322 300,390 228,572 Z" fill="var(--charcoal)"/>
      <path class="dark-field" d="M262,572 C310,420 440,350 640,338 C780,330 880,318 1000,300 L1000,572 Z" fill="var(--charcoal)"/>
      <rect class="house-photo" x="640" y="195" width="320" height="150" rx="6" fill="url(#house-tone)" role="img" aria-label="Photograph of a two-storey suburban house with gabled roof and front garden"/>
    </svg>

    <div class="brand">
      <span class="brand-mark"></span>
      <span class="brand-name">WALSH &amp; BRAND PTY LTD.</span>
    </div>

    <h1 class="names">Owen Walsh and Lucy Brand</h1>
    <p class="role">Onsite Manager &amp; Sales Agents</p>

    <ul class="contact-list">
      <li>
        <svg class="contact-icon" viewBox="0 0 22 22"><rect width="22" height="22" rx="3" fill="var(--paper)"/><path d="M7 5l3 3-1.5 1.5c1 2 2 3 4 4L14 12l3 3-2 2c-5 0-10-5-10-10z" fill="var(--charcoal)"/></svg>
        <span>07 5948 2063</span>
      </li>
      <li>
        <svg class="contact-icon" viewBox="0 0 22 22"><rect width="22" height="22" rx="3" fill="var(--paper)"/><rect x="7" y="4" width="8" height="14" rx="1.5" fill="var(--charcoal)"/><rect x="8.5" y="6" width="5" height="8" fill="var(--paper)"/></svg>
        <span>0431 857 219</span>
      </li>
      <li>
        <svg class="contact-icon" viewBox="0 0 22 22"><rect width="22" height="22" rx="3" fill="var(--paper)"/><path d="M11 4a5 5 0 0 1 5 5c0 4-5 9-5 9s-5-5-5-9a5 5 0 0 1 5-5z" fill="var(--charcoal)"/><circle cx="11" cy="9" r="2" fill="var(--paper)"/></svg>
        <span>3/42 Marlow Crescent, FERNLEA QLD 4213</span>
      </li>
    </ul>
  </article>
</body>
</html>
```